FinTech company looking to revamp and expand client-facing interface for our financial models

Pellworth Engines currently has a very simple website that allows clients to interact with our financial models. We are looking to completely redesign the current site and add several extra pages to provide extra functionality. We want the design to have a modern, slick feel, that will work on both a desktop or a tablet. It should be straightforward for clients to move between different pages at any time, and clear from the layout how to interact with the more advanced features. We have included screenshots of existing pages in the attached design brief, as well as sketches of the functionality required by the new pages, but can't provide a direct link to the current site.
Target Market(s)
Professional investors that will be paying to access the interface
Industry/Entity Type
Finance
Number of Pages Required
4 page
Colors
Designer to choose colors to be used in the design.
Look and feel
Each slider illustrates characteristics of the customer's brand and the style your logo design should communicate.

```html
<!DOCTYPE html>
<html lang="en">
<head>
<meta charset="utf-8">
<title>QMERE · Models</title>
<link href="https://fonts.googleapis.com/css2?family=Open+Sans:wght@400;600;700&display=swap" rel="stylesheet">
<style>
:root{
  --teal:#2fae96;
  --teal-soft:#e3f3ef;
  --ink:#111;
  --dark:#1c1c1c;
  --page:#f2f2f2;
  --panel:#e9e9e9;
  --tab-active:#c9c9c9;
  --line:#d9d9d9;
  --white:#fff;
  --navy:#1d3a66;
}
*{box-sizing:border-box;margin:0;padding:0}
html,body{width:1200px;height:678px;overflow:hidden}
body{font-family:"Open Sans",Arial,sans-serif;color:var(--ink);background:var(--page);position:relative}

.topbar{position:absolute;left:0;top:0;width:1200px;height:55px;background:var(--white);box-shadow:0 3px 10px rgba(0,0,0,.12);z-index:3}
.brand{position:absolute;left:67px;top:0;height:55px;line-height:55px;font-weight:700;font-size:17px;letter-spacing:.3px}
.nav-item{position:absolute;top:0;height:55px;display:flex;align-items:center;justify-content:center;gap:7px;font-weight:700;font-size:13px;border-right:1px solid #eee}
.nav-item.active{background:var(--teal);color:var(--white)}
.nav-item svg{width:22px;height:22px}

.workspace{position:absolute;left:0;top:143px;width:1200px;height:535px;background:linear-gradient(#e6e6e6,#f4f4f4 40%,#f7f7f7)}

.tab{position:absolute;bottom:535px;height:auto;display:flex;align-items:center;justify-content:center;font-weight:700;font-size:12.5px;background:var(--white);border-radius:4px 4px 0 0}
.tab.plain{background:transparent}
.tab.active{background:var(--tab-active)}
.tab-arrow{position:absolute;left:1099px;top:111px;width:36px;height:32px;background:var(--white);display:flex;align-items:center;justify-content:center;border-radius:4px 4px 0 0}
.tab-add{position:absolute;left:1140px;top:111px;width:36px;height:32px;background:var(--white);display:flex;align-items:center;justify-content:center;border-radius:4px 4px 0 0}

.filters{position:absolute;left:0;top:235px;width:46px;height:176px;background:#d3d3d3;border-radius:0 5px 5px 0}
.filters span{position:absolute;left:10px;top:88px;transform:translate(0,-50%) rotate(-90deg);transform-origin:center;font-weight:700;font-size:13px;letter-spacing:.5px;width:28px;text-align:center}
.filters-toggle{position:absolute;left:33px;top:310px;width:27px;height:27px;border-radius:50%;background:var(--navy);border:2px solid var(--white);box-shadow:0 0 0 1px #999;display:flex;align-items:center;justify-content:center}

.export{position:absolute;left:1085px;top:183px;display:flex;align-items:center;gap:6px;color:var(--teal);font-weight:700;font-size:16px}

.models{position:absolute;left:97px;top:217px;width:1071px;border-collapse:collapse;background:var(--white);box-shadow:0 2px 10px rgba(0,0,0,.12);border-radius:6px;overflow:hidden;font-size:15.5px}
.models th{height:65px;color:var(--white);font-weight:700;font-size:15.5px;text-align:center;background:var(--teal);border-right:1px solid rgba(255,255,255,.25)}
.models th.key{background:var(--dark)}
.models td{height:64.6px;padding:0 5px;border-right:1px solid var(--line);line-height:1.4}
.models td.id{padding-left:16px}
.models td.sector{padding-left:16px}
.models tr:nth-child(even) td{background:var(--teal-soft)}
.models td.num{padding-left:4px}
</style>
</head>
<body>

<header class="topbar">
  <div class="brand">QMERE</div>
  <div class="nav-item active" style="left:180px;width:83px">250D</div>
  <div class="nav-item" style="left:263px;width:83px">83D</div>
  <div class="nav-item" style="left:346px;width:83px">42D</div>
  <div class="nav-item" style="left:429px;width:125px"></div>
  <div class="nav-item active" style="left:554px;width:131px">
    <svg viewBox="0 0 24 24" fill="none" stroke="#fff" stroke-width="2"><path d="M3 11 12 3l9 8"/><path d="M5 10v11h5v-6h4v6h5V10"/></svg>MODELS</div>
  <div class="nav-item" style="left:685px;width:162px">
    <svg viewBox="0 0 24 24" fill="#222"><circle cx="12" cy="12" r="2"/><g><circle cx="12" cy="4" r="1.4"/><circle cx="12" cy="20" r="1.4"/><circle cx="4" cy="12" r="1.4"/><circle cx="20" cy="12" r="1.4"/><circle cx="6.3" cy="6.3" r="1.3"/><circle cx="17.7" cy="6.3" r="1.3"/><circle cx="6.3" cy="17.7" r="1.3"/><circle cx="17.7" cy="17.7" r="1.3"/><circle cx="12" cy="8" r="1"/><circle cx="12" cy="16" r="1"/><circle cx="8" cy="12" r="1"/><circle cx="16" cy="12" r="1"/></g></svg>SENSITIVITIES</div>
  <div class="nav-item" style="left:847px;width:150px">
    <svg viewBox="0 0 24 24" fill="none" stroke="#222" stroke-width="1.8"><circle cx="7" cy="7" r="4"/><circle cx="17" cy="7" r="4"/><circle cx="7" cy="17" r="4"/><circle cx="17" cy="17" r="4"/></svg>PORTFOLIO</div>
  <div class="nav-item" style="left:997px;width:138px">
    <svg viewBox="0 0 24 24" fill="none" stroke="#222" stroke-width="1.8"><rect x="2" y="3" width="20" height="18"/><path d="M4 17l5-6 4 4 4-6 3 3"/></svg>BACKTEST</div>
</header>

<nav class="tabs">
  <div class="tab plain" style="left:65px;top:111px;width:146px;height:32px">EQUITIES</div>
  <div class="tab" style="left:212px;top:111px;width:143px;height:32px">ETFS</div>
  <div class="tab" style="left:360px;top:101px;width:143px;height:42px">PAIRS</div>
  <div class="tab active" style="left:508px;top:92px;width:143px;height:51px">ETF PAIRS</div>
  <div class="tab" style="left:655px;top:101px;width:143px;height:42px">FACTORS</div>
  <div class="tab" style="left:803px;top:111px;width:143px;height:32px">NEW TAB TITLE #1</div>
  <div class="tab" style="left:951px;top:111px;width:143px;height:32px">NEW TAB TITLE #2</div>
  <div class="tab-arrow"><svg width="14" height="18" viewBox="0 0 14 18"><path d="M3 2l8 7-8 7" fill="none" stroke="#888" stroke-width="3"/></svg></div>
  <div class="tab-add"><svg width="22" height="22" viewBox="0 0 22 22" fill="none" stroke="#777" stroke-width="1.6"><circle cx="11" cy="11" r="9.5"/><path d="M11 6v10M6 11h10"/></svg></div>
</nav>

<main class="workspace"></main>

<aside class="filters"><span>FILTERS</span></aside>
<div class="filters-toggle"><svg width="14" height="14" viewBox="0 0 14 14" fill="none" stroke="#fff" stroke-width="2"><path d="M2 7h10M8 3l4 4-4 4"/></svg></div>

<div class="export">
  <svg width="24" height="22" viewBox="0 0 24 22" fill="none" stroke="#2fae96" stroke-width="2"><path d="M10 5H3v15h15v-6"/><path d="M8 15c1-6 5-9 12-9M16 2l4 4-4 4"/></svg>Export
</div>

<table class="models">
  <colgroup>
    <col style="width:92px"><col style="width:129px"><col style="width:106px"><col style="width:79px">
    <col style="width:83px"><col style="width:83px"><col style="width:83px"><col style="width:83px">
    <col style="width:83px"><col style="width:83px"><col style="width:83px"><col style="width:83px">
  </colgroup>
  <thead>
    <tr>
      <th class="key">ID <svg width="10" height="8" viewBox="0 0 10 8"><path d="M1 2l4 4 4-4" fill="none" stroke="#fff" stroke-width="1.8"/></svg></th>
      <th class="key">Sector</th><th class="key">Time</th>
      <th>Quality</th><th>Stat 1</th><th>Stat 2</th><th>Stat 3</th><th>Stat 4</th><th>Stat 5</th><th>Stat 6</th><th>Stat 7</th><th>Stat 8</th>
    </tr>
  </thead>
  <tbody>
    <tr><td class="id">Model 1</td><td class="sector">Materials</td><td class="num">2019-07-03 12:15:00.000</td><td class="num">30.2288</td><td class="num">2.01574</td><td class="num">23.305</td><td class="num">-0.149368</td><td class="num">22.3054</td><td class="num">4.63714</td><td class="num">0.945706</td><td class="num">2.81949</td><td class="num">2.60858</td></tr>
    <tr><td class="id">Model 2</td><td class="sector">Industrials</td><td class="num">2019-07-03 12:15:00.000</td><td class="num">32.8694</td><td class="num">0.87307</td><td class="num">32.185</td><td class="num">-0.033692</td><td class="num">33.9911</td><td class="num">11.5693</td><td class="num">-0.472968</td><td class="num">-0.830458</td><td class="num">6.80646</td></tr>
    <tr><td class="id">Model 3</td><td class="sector">Consumer Discretionary</td><td class="num">2019-07-03 12:15:00.000</td><td class="num">1.66002</td><td class="num">-0.569222</td><td class="num">159.814</td><td class="num">0.0252328</td><td class="num">172.616</td><td class="num">10.2875</td><td class="num">-0.750396</td><td class="num">-0.385309</td><td class="num">4.69146</td></tr>
    <tr><td class="id">Model 4</td><td class="sector">Information Technology</td><td class="num">2019-07-03 12:15:00.000</td><td class="num">45.6856</td><td class="num">0.412148</td><td class="num">202.488</td><td class="num">0.0084923</td><td class="num">205.834</td><td class="num">11.9094</td><td class="num">-0.137913</td><td class="num">0.449595</td><td class="num">3.85106</td></tr>
    <tr><td class="id">Model 5</td><td class="sector">Information Technology</td><td class="num">2019-07-03 12:15:00.000</td><td class="num">75.7733</td><td class="num">7.06728</td><td class="num">188.605</td><td class="num">0.016913</td><td class="num">161.665</td><td class="num">3.82241</td><td class="num">0.981019</td><td class="num">1.29847</td><td class="num">3.34927</td></tr>
  </tbody>
</table>

</body>
</html>
```